Wordpress Design Project - LumaFernSites

I would like our existing old website at www.lumafernsites.example to be redesigned to a more modern attractive site using Wordpress, a total of 5 web pages. And also installed onto our new web hosting site. Please visit the existing website using Microsoft Internet explorer to see the content.
The new site must be compatible with all popular web browsers and mobile devices (if possible).
There should be a contact button available on each page with an associated form in case an interested person wants to contact us. This form must be spam proof not allowing automated crawlers from activating it.
Updates

There are only 5 pages web pages to this LumaFernSites project.

Industry/Entity Type

Internet

```html
<!DOCTYPE html>
<html lang="en">
<head>
<meta charset="utf-8">
<title>LumaFernSites</title>
<link href="https://fonts.googleapis.com/css2?family=Open+Sans:wght@400;600;700;800&family=Oswald:wght@500;600&display=swap" rel="stylesheet">
<style>
:root{
  --sky:#cfe6f5;
  --sky-deep:#8fc3e6;
  --navy:#0d3f7a;
  --navy-dark:#082c57;
  --blue:#1a78c2;
  --orange:#f29a1f;
  --orange-dark:#d9760b;
  --text:#555b63;
  --light:#f3f7fb;
  --white:#ffffff;
  --line:#d7e1ea;
}
*{box-sizing:border-box;margin:0;padding:0}
html,body{width:861px;height:1200px;overflow:hidden}
body{font-family:"Open Sans",Arial,sans-serif;color:var(--text);font-size:8px;line-height:1.45;
  background:linear-gradient(180deg,var(--sky-deep) 0,var(--sky) 420px,#e8f3fb 1200px);}
.page{position:absolute;left:28px;top:0;width:805px;height:1200px;background:var(--white);box-shadow:0 0 12px rgba(0,40,90,.18)}
.header{position:relative;height:112px}
.brand{position:absolute;left:22px;top:26px;display:flex;align-items:center;gap:8px}
.brand-dot{width:26px;height:26px;border-radius:50%;background:var(--blue)}
.brand-name{font-size:27px;font-weight:800;color:var(--navy);letter-spacing:-.5px}
.brand-tag{position:absolute;left:56px;top:60px;font-size:7px;color:var(--text)}
.support{position:absolute;right:20px;top:16px;width:140px;background:var(--navy);color:var(--white);text-align:center;border-radius:4px;padding:6px 0 7px}
.support-title{font-family:"Oswald",sans-serif;font-size:20px;font-weight:600;background:var(--white);color:var(--navy);margin:0 10px 4px;border-radius:3px;line-height:1.25}
.support-free{font-size:11px;font-weight:700;line-height:1.2}
.support-phone{font-size:11px;font-weight:700;line-height:1.2}
.nav{position:absolute;top:112px;left:0;width:805px;height:26px;background:linear-gradient(var(--blue),var(--navy));display:flex}
.nav a{color:var(--white);text-decoration:none;font-size:7.5px;font-weight:700;text-transform:uppercase;line-height:26px;padding:0 22px;border-right:1px solid rgba(255,255,255,.25)}
.nav a.active{background:var(--orange)}
.hero{position:absolute;top:146px;left:20px;width:765px;height:302px;background:linear-gradient(180deg,#1c5ea8 0,#3d8bd0 45%,#8cc2e6 100%);overflow:hidden}
.hero-copy{position:absolute;right:28px;top:128px;text-align:right;font-family:"Oswald",sans-serif;color:var(--white);font-size:33px;font-weight:600;line-height:1.12;text-shadow:0 2px 4px rgba(0,0,0,.35)}
.hero-dots{position:absolute;bottom:10px;left:50%;transform:translateX(-50%);display:flex;gap:5px}
.hero-dots span{width:7px;height:7px;border-radius:50%;background:rgba(255,255,255,.6)}
.hero-dots span:first-child{background:var(--orange)}
.intro{position:absolute;top:466px;left:20px;width:510px}
.intro h2{font-size:12px;font-weight:400;color:var(--text);margin:0 0 8px}
.intro h2 b{color:var(--blue);font-weight:700;font-size:15px}
.intro p{margin-bottom:8px}
.intro h2.why{margin-top:14px}
.quote{position:absolute;top:470px;right:20px;width:224px;height:300px;background:var(--light);border:1px solid var(--line);border-radius:4px;padding:0 12px}
.quote-head{margin:10px -4px 10px;background:linear-gradient(var(--orange),var(--orange-dark));color:var(--white);font-weight:700;font-size:12px;height:28px;border-radius:4px;display:flex;align-items:center;gap:8px;padding-left:20px}
.quote-head svg{flex:none}
.field{height:17px;background:var(--white);border:1px solid var(--line);border-radius:2px;margin-bottom:7px;font-size:6.5px;color:#9aa3ab;padding-left:5px;line-height:15px}
.field.area{height:44px}
.captcha{display:flex;gap:6px;margin-bottom:8px}
.captcha-box{width:100px;height:22px;background:#e3e7ea;border:1px solid var(--line)}
.captcha .field{flex:1;margin:0;height:22px}
.submit{display:inline-block;background:var(--orange);color:var(--white);font-weight:700;font-size:8px;padding:4px 12px;border-radius:3px}
.services{position:absolute;top:792px;left:20px;width:765px}
.services-title{text-align:center;font-size:9px;font-weight:700;color:var(--navy);text-transform:uppercase;border-top:1px solid var(--line);padding-top:9px;margin-bottom:8px}
.cards{display:flex;gap:22px}
.card{flex:1;background:var(--light);border:1px solid var(--line);padding:10px 10px 12px;height:176px}
.card h3{font-size:8px;font-weight:800;color:#333;text-transform:uppercase;margin-bottom:7px}
.card-media{height:86px;margin-bottom:7px}
.card-media.voip{background:linear-gradient(135deg,#3f4a55,#a8b4bf)}
.card-media.lan{background:linear-gradient(135deg,#2b6fb0,#b9d6ee)}
.card-media.help{background:linear-gradient(135deg,#c9d3dc,#6e8296)}
.card p{font-size:7px;margin-bottom:4px}
.card .more{font-size:7px;color:var(--blue);font-weight:600}
.footer{position:absolute;top:1000px;left:0;width:805px;height:168px;background:linear-gradient(var(--navy),var(--navy-dark));color:#d7e6f5;padding:14px 20px}
.footer-name{font-weight:700;color:var(--white);font-size:9px;margin-bottom:4px}
.footer-address{font-size:7px;line-height:1.6}
.map{position:absolute;left:300px;top:14px;width:230px;height:130px;background:linear-gradient(135deg,#c6d9c3,#e6efe2)}
.social{position:absolute;right:22px;top:14px;width:170px}
.social-title{font-size:8px;font-weight:600;color:var(--white);margin-bottom:8px}
.social-row{display:flex;gap:6px}
.social-row span{width:18px;height:18px;border-radius:3px;background:var(--blue)}
.bottom{position:absolute;top:1168px;left:0;width:805px;height:22px;background:var(--navy-dark);color:#9fb7d0;font-size:6.5px;display:flex;align-items:center;justify-content:space-between;padding:0 20px;border-top:1px solid rgba(255,255,255,.15)}
</style>
</head>
<body>
<div class="page">
  <header class="header">
    <div class="brand"><span class="brand-dot"></span><span class="brand-name">LumaFernSites</span></div>
    <div class="brand-tag">Connecting Web Technology Solutions</div>
    <div class="support">
      <div class="support-title">24x7 SUPPORT</div>
      <div class="support-free">TOLL FREE NO:</div>
      <div class="support-phone">(011) 5550 1234</div>
    </div>
  </header>
  <nav class="nav">
    <a class="active">Home</a>
    <a>Support Services</a>
    <a>Telephone VoIP Solutions</a>
    <a>IP, LAN &amp; Intranet</a>
    <a>Contact</a>
  </nav>

  <section class="hero" role="img" aria-label="Man in a field reaching toward a bright blue sky filled with web symbols">
    <div class="hero-copy">WIRED/WIRELESS<br>INTERNET/INTRANET</div>
    <div class="hero-dots"><span></span><span></span><span></span></div>
  </section>

  <section class="intro">
    <h2>welcome to <b>LumaFernSites</b></h2>
    <p>LumaFernSites provides complete telephone VoIP PBX solutions for businesses large and small.</p>
    <p>Our team of telecom engineers will design and install the best business telephone VoIP PBX solution for your requirements. System features include standard and advanced PBX call control options, video telephone calling, toll free calling and more, all backed by friendly support staff every hour of every day.</p>
    <p>We also provide complete wired and wireless LAN/WAN/VPN solutions and services for data, voice and video across various industries, including hospitality, education, commercial and residential, with fully managed network monitoring and round the clock technical support for every client we serve.</p>
    <h2 class="why">why <b>LumaFernSites?</b></h2>
    <p>LumaFernSites provides state of the art VoIP PBX phone solutions with products tailored to small, medium and large businesses. Our engineering team will assess your communication requirements and provide you with the best telephone solution for your business needs.</p>
    <p>LumaFernSites will be there for you during the whole process, from the initial quote all the way through installation and support. Your satisfaction is our commitment to you.</p>
  </section>

  <aside class="quote">
    <div class="quote-head">
      <svg width="16" height="16" viewBox="0 0 16 16"><circle cx="8" cy="8" r="7.5" fill="#fff"/><path d="M4.5 8.2l2.3 2.3 4.7-4.8" stroke="#d9760b" stroke-width="1.8" fill="none"/></svg>
      GET A FREE QUOTE
    </div>
    <div class="field">Your Name</div>
    <div class="field">Your Phone No</div>
    <div class="field">Your Email Id</div>
    <div class="field area">Your Message or Queries</div>
    <div class="captcha"><div class="captcha-box"></div><div class="field">Enter Code</div></div>
    <span class="submit">Submit</span>
  </aside>

  <section class="services">
    <div class="services-title">Our Services</div>
    <div class="cards">
      <article class="card">
        <h3>Telephone VoIP Solutions</h3>
        <div class="card-media voip" role="img" aria-label="Office desk phone handset"></div>
        <p>Business phone systems with clear calls, easy setup and lower monthly costs.</p>
        <span class="more">» Read More</span>
      </article>
      <article class="card">
        <h3>IP, LAN &amp; Internet</h3>
        <div class="card-media lan" role="img" aria-label="Network cables plugged into a switch"></div>
        <p>Fast wired and wireless networks built and managed for your whole site.</p>
        <span class="more">» Read More</span>
      </article>
      <article class="card">
        <h3>24x7 Help/Support</h3>
        <div class="card-media help" role="img" aria-label="Support agent wearing a headset"></div>
        <p>Our friendly support team is ready to help you at any hour, every day.</p>
        <span class="more">» Read More</span>
      </article>
    </div>
  </section>

  <footer class="footer">
    <div class="footer-name">LumaFernSites</div>
    <div class="footer-address">14 Harbour Lane,<br>Westfield, WF2 7QL<br>Email: hello@lumafernsites.example<br>Phone: (011) 5550 1234</div>
    <div class="map" role="img" aria-label="Street map showing the office location"></div>
    <div class="social">
      <div class="social-title">Keep In Touch With Us</div>
      <div class="social-row"><span></span><span></span><span></span><span></span></div>
    </div>
  </footer>
  <div class="bottom">
    <span>© 2014, All Rights Reserved</span>
    <span>Terms &amp; Conditions &nbsp;|&nbsp; Privacy &nbsp;|&nbsp; Help</span>
    <span>Design &amp; Hosting by LumaFernSites</span>
  </div>
</div>
</body>
</html>
```